IT company developing solutions for air cargo industry is looking for a new website

We are a professional IT company developing solutions for air cargo industry worldwide.

We are looking to update and completely redesign our current webpages: https://www.brisklane.cz/

What we like about our current pages are the animated graphics on the home page. These could stay, but not a must.

The design of the new pages should be very modern, clean, unique, creative, professional, and to make a statement. We are looking for animated graphics, cool and interesting interactions, cascading layers, etc.

Our company logo is yellow, gray and black. You don’t necessarily have to stick to this colour scheme, however the corporate colors should work well with the overal design of the web pages.
Dark mode pages are also an option.

The scope of the project would include creating a:

• Header
• Footer
• Landing page
• Navigation bar (8 tabs)
• Subpages (10)

In the first stage we are looking only for the header / footer / landing page with navigaton bar / Solutions page design.
As a second round, finalists might be asked to submit another section of the website to see their consistency in terms of the look and feel proposed for the Homepage and Solutions’ pages.
The winning designer will then complete the rest of the pages.

Attached you will find a brief for the first scope of the project. Please read the note section on slide nr. 3 carefully to understand, what we exactly are looking for to achieve.

Industry/Entity Type

Aviation

Number of Pages Required

1 page

Requirements
Must have
• See brief
Nice to have
• See brief
Should not have
• See brief

```html
<!DOCTYPE html>
<html lang="en">
<head>
<meta charset="utf-8">
<title>Brisk Lane – Air Cargo IT Solutions</title>
<link href="https://fonts.googleapis.com/css2?family=Fira+Sans:wght@400;500;700&family=Open+Sans:wght@400;600&display=swap" rel="stylesheet">
<style>
:root{
  --gold:#f5c116;
  --ink:#111;
  --grey:#555;
  --footer:#2a2a2a;
  --white:#fff;
  --placeholder:#8fa3b3;
}
*{box-sizing:border-box;margin:0;padding:0}
html,body{width:940px;height:1200px;overflow:hidden;background:var(--white)}
body{font-family:"Fira Sans",sans-serif;color:var(--ink);position:relative}
.site-header{height:62px;display:flex;align-items:center;padding:0 87px;justify-content:space-between}
.brand{display:flex;align-items:center;gap:10px;font-weight:500;font-size:18px;color:#333}
.brand-mark{width:30px;height:30px;background:var(--gold)}
.main-nav{display:flex;gap:19px;font-family:"Open Sans",sans-serif;font-size:9.4px;color:#222;text-transform:uppercase}
.main-nav .has-menu::after{content:"";display:inline-block;margin-left:3px;border:3px solid transparent;border-top-color:#888;vertical-align:-1px}
.tagline-bar{height:44px;background:var(--gold);color:var(--white);font-weight:500;font-size:15.5px;display:flex;align-items:center;justify-content:center}
.hero{position:relative;height:420px;overflow:hidden}
.hero-photo{position:absolute;inset:0;background:linear-gradient(90deg,#ececec 0%,#dcdcdc 55%,#9a9a9a 70%,#c9a23a 100%)}
.hero-globe{position:absolute;left:462px;top:47px;width:324px;height:324px;border-radius:50%;background:var(--placeholder)}
.hero-copy{position:absolute;left:86px;top:60px}
.hero-title{font-weight:400;font-size:30px;line-height:38px;color:#111;width:380px}
.hero-title strong{font-weight:700;display:block}
.hero-text{margin-top:12px;width:325px;font-family:"Open Sans",sans-serif;font-size:10.8px;line-height:22px;color:#333}
.btn{display:inline-block;margin-top:18px;background:var(--gold);color:var(--white);font-weight:500;font-size:12px;width:111px;height:32px;line-height:32px;text-align:center;border-radius:4px}
.claim{text-align:center;margin-top:45px;font-size:28.5px;line-height:38px;font-weight:400}
.claim strong{display:block;font-weight:700}
.facts-label{text-align:center;margin-top:26px;font-family:"Open Sans",sans-serif;font-size:16px;color:var(--grey)}
.facts{position:absolute;left:115px;top:728px;display:grid;grid-template-columns:repeat(3,220px);gap:23px 25px}
.fact{height:118px;border-radius:10px;background:var(--white);box-shadow:0 2px 8px rgba(0,0,0,.08);border:1px solid #f0f0f0;display:flex;flex-direction:column;align-items:center;justify-content:center;text-align:center}
.fact-value{color:var(--gold);font-weight:700;font-size:27px;line-height:30px}
.fact-label{font-size:15px;line-height:19px;color:#222;font-weight:400}
.site-footer{position:absolute;left:0;top:1063px;width:940px;height:137px;background:var(--footer);display:flex;flex-direction:column;align-items:center;padding-top:37px;color:var(--white)}
.site-footer .brand{color:var(--white)}
.copyright{margin-top:20px;font-size:12px}
</style>
</head>
<body>
<header class="site-header">
  <div class="brand"><span class="brand-mark"></span>Brisk Lane</div>
  <nav class="main-nav">
    <span>Industries</span><span class="has-menu">Solutions</span><span>Operational Support</span><span>Case Studies</span><span>Testimonials</span><span>News</span><span class="has-menu">About Us</span>
  </nav>
</header>
<div class="tagline-bar">Affordable IT Solutions That Revolutionize Tomorrow’s Air Cargo Today</div>
<section class="hero">
  <div class="hero-photo" role="img" aria-label="Air cargo apron with aircraft and cargo pallets"></div>
  <div class="hero-globe" role="img" aria-label="Globe showing flight route with connected locations"></div>
  <div class="hero-copy">
    <h1 class="hero-title">Seamlessly connecting the<br>air cargo industry from <strong>Manila to Tahiti</strong></h1>
    <p class="hero-text">Blending decades of air cargo knowledge with end-to-end IT solutions. Whether you are an Airline, GSA, GHA, Forwarder or E-commerce Operator, our expertise can elevate your daily workflows, cutting down on expenses, time, and errors.</p>
    <span class="btn">Learn More</span>
  </div>
</section>
<h2 class="claim">We are not IT tech experts attempting to do cargo!<strong>We are cargo experts with programming skills!</strong></h2>
<p class="facts-label">FACTS</p>
<div class="facts">
  <div class="fact"><span class="fact-value">2014</span><span class="fact-label">Established</span></div>
  <div class="fact"><span class="fact-value">22</span><span class="fact-label">Employees</span></div>
  <div class="fact"><span class="fact-value">11,500,000 +</span><span class="fact-label">Nr. of Annual Electronic<br>Exchanges</span></div>
  <div class="fact"><span class="fact-value">18</span><span class="fact-label">Countries covered</span></div>
  <div class="fact"><span class="fact-value">20+</span><span class="fact-label">Connected Clients</span></div>
  <div class="fact"><span class="fact-value">350,000 +</span><span class="fact-label">Nr. of Annual AWBs</span></div>
</div>
<footer class="site-footer">
  <div class="brand"><span class="brand-mark"></span>Brisk Lane</div>
  <p class="copyright">2024 Brisk Lane. All Rights Reserved.</p>
</footer>
</body>
</html>
```